Brightmill Data Works

Our company is about IT hardwares and IT solutions. IT hardware such as PC, RAMS, storage and servers. IT solutions such as project management, BA. We are also selling new technology too.

Target Market(s)

Consumer, Small to Medium Business, Corporate

Requirements
Must have
• The business card must have the following:
• Name:
• Title:
• Contact Number:
• Email address:
• Website:
• Color: Must match the logo color upgrade

```html
<!DOCTYPE html>
<html lang="en">
<head>
<meta charset="utf-8">
<title>Brightmill Data Works – Business Card</title>
<link rel="stylesheet" href="https://fonts.googleapis.com/css2?family=Open+Sans:wght@400;600;700&display=swap">
<style>
  :root {
    --backdrop: #666666;
    --card-white: #ffffff;
    --orange-light: #dc9a42;
    --orange-deep: #c4682a;
    --ink-dark: #3f3f3f;
    --ink-light: #ffffff;
  }
  html, body {
    margin: 0;
    padding: 0;
    width: 1200px;
    height: 802px;
    overflow: hidden;
    background: var(--backdrop);
    font-family: "Open Sans", Arial, sans-serif;
  }
  .canvas {
    position: relative;
    width: 1200px;
    height: 802px;
  }
  .card {
    position: absolute;
    top: 274px;
    width: 443px;
    height: 265px;
    box-sizing: border-box;
  }
  .card--contact {
    left: 136px;
    background: linear-gradient(180deg, var(--orange-light) 0%, var(--orange-deep) 100%);
    color: var(--ink-light);
    text-align: right;
    padding: 0 26px 0 0;
  }
  .card--brand {
    left: 624px;
    background: var(--card-white);
    display: flex;
    align-items: center;
    justify-content: center;
    gap: 10px;
  }
  .person {
    position: absolute;
    right: 26px;
    top: 70px;
  }
  .person__name {
    margin: 0;
    font-size: 16.5px;
    font-weight: 600;
    letter-spacing: 0.2px;
    line-height: 1.1;
  }
  .person__title {
    margin: 0;
    font-size: 13px;
    font-weight: 400;
    line-height: 1.3;
  }
  .contacts {
    position: absolute;
    right: 26px;
    top: 147px;
    margin: 0;
    padding: 0;
    list-style: none;
    font-size: 13px;
    line-height: 16.5px;
  }
  .contacts li {
    display: flex;
    justify-content: flex-end;
    align-items: center;
    gap: 3px;
  }
  .contacts svg {
    width: 10px;
    height: 10px;
    fill: var(--ink-light);
  }
  .brand__dot {
    width: 14px;
    height: 14px;
    border-radius: 50%;
    background: var(--orange-deep);
  }
  .brand__name {
    margin: 0;
    font-size: 25px;
    font-weight: 700;
    color: var(--ink-dark);
    letter-spacing: 0.3px;
  }
</style>
</head>
<body>
<main class="canvas">
  <section class="card card--contact" aria-label="Contact side">
    <div class="person">
      <p class="person__name">ELENA MARSH</p>
      <p class="person__title">Managing Director</p>
    </div>
    <ul class="contacts">
      <li>044-210 387 556
        <svg viewBox="0 0 10 10" aria-hidden="true"><path d="M1 3.2C1 2 2.5 1.5 5 1.5S9 2 9 3.2L7.4 3.8 6.8 3H3.2L2.6 3.8ZM2.6 4.4h4.8L8.5 8.5h-7Z"/></svg>
      </li>
      <li>hello@brightmill.com
        <svg viewBox="0 0 10 10" aria-hidden="true"><path d="M0.5 2h9v6h-9Zm0.8 0.6L5 5.4 8.7 2.6Z" fill-rule="evenodd"/></svg>
      </li>
      <li>www.brightmill.com
        <svg viewBox="0 0 10 10" aria-hidden="true"><circle cx="5" cy="5" r="4.5"/><path d="M3 3.5h2.5v2h-2Zm3 2.5h1.5v1.5h-1Z" fill="#c4682a"/></svg>
      </li>
    </ul>
  </section>

  <section class="card card--brand" aria-label="Brand side">
    <span class="brand__dot" aria-hidden="true"></span>
    <p class="brand__name">Brightmill Data Works</p>
  </section>
</main>
</body>
</html>
```